Industrial Company-Pop-Up Banner Design for Demolition and Infrastructure Company

Hi-
We need to create 2 pop-up banners for our company. They will both have the same logo, but different photos. We would like to have the colors white, red, and black and feature a modern design. I have attached some inspiration photos.

Target Market(s)

Trade Show/Job Fair Audience

Industry/Entity Type

construction, industrial

Font styles to use
Sans Serif

Colors
EB3D1F
EC4F4E
F09395
F8D3D4
FCEDEE

Requirements
Must have
• 2 versions, each with different photos but same design. Logo, Red, Black, and White Color Scheme, Modern Design
Nice to have
• Modern Design similar to the inspiration photos

```html
<!DOCTYPE html>
<html lang="en">
<head>
<meta charset="utf-8">
<title>R.K. Holloway Companies – Pop-Up Banners</title>
<link href="https://fonts.googleapis.com/css2?family=Roboto:wght@500;700&family=Kaushan+Script&display=swap" rel="stylesheet">
<style>
  :root {
    --canvas: #ececec;
    --white: #ffffff;
    --ink: #1c1c1c;
    --charcoal: #333333;
    --red: #eb3d1f;
    --red-soft: #ec4f4e;
    --red-deep: #a32b38;
    --pink: #f09395;
    --blush: #f8d3d4;
  }
  html, body {
    margin: 0;
    width: 1200px;
    height: 800px;
    overflow: hidden;
    background: var(--canvas);
    font-family: "Roboto", Arial, sans-serif;
  }
  .stage {
    position: relative;
    width: 1200px;
    height: 800px;
  }
  .banner {
    position: absolute;
    top: 55px;
    height: 690px;
    box-shadow: 0 6px 18px rgba(0,0,0,0.12);
  }
  .banner--collage { left: 300px; width: 294px; }
  .banner--wave { left: 640px; width: 266px; }
  .banner svg {
    position: absolute;
    inset: 0;
    width: 100%;
    height: 100%;
    display: block;
  }
  .brand {
    position: absolute;
    left: 0;
    right: 0;
    display: flex;
    align-items: center;
    justify-content: center;
    gap: 7px;
    font-weight: 700;
    color: var(--red-soft);
    letter-spacing: 0.02em;
    white-space: nowrap;
  }
  .brand__mark {
    background: var(--red-soft);
  }
  .tagline {
    position: absolute;
    left: 0;
    right: 0;
    text-align: center;
    margin: 0;
    white-space: nowrap;
  }
  .tagline__lead,
  .tagline__since {
    display: block;
    font-weight: 500;
    line-height: 1.15;
  }
  .tagline__accent {
    display: block;
    font-family: "Kaushan Script", cursive;
    line-height: 1;
  }

  /* collage banner */
  .banner--collage .brand { top: 550px; font-size: 15px; }
  .banner--collage .brand__mark { width: 11px; height: 11px; }
  .banner--collage .tagline { top: 593px; color: var(--white); }
  .banner--collage .tagline__lead { font-size: 16px; }
  .banner--collage .tagline__accent { font-size: 34px; margin: 0 0 1px; }
  .banner--collage .tagline__since { font-size: 16px; }

  /* wave banner */
  .banner--wave .brand { top: 446px; font-size: 16px; }
  .banner--wave .brand__mark { width: 12px; height: 12px; }
  .banner--wave .tagline { top: 505px; color: var(--ink); }
  .banner--wave .tagline__lead { font-size: 19px; }
  .banner--wave .tagline__accent { font-size: 44px; margin: 0 0 1px; }
  .banner--wave .tagline__since { font-size: 19px; }
</style>
</head>
<body>
<main class="stage">

  <section class="banner banner--collage">
    <svg viewBox="0 0 450 1055" preserveAspectRatio="none">
      <defs>
        <linearGradient id="sky-site" x1="0" y1="0" x2="1" y2="1">
          <stop offset="0" stop-color="#9fb6c9"/><stop offset="0.6" stop-color="#8a9aa3"/><stop offset="1" stop-color="#6e7c76"/>
        </linearGradient>
        <linearGradient id="green-site" x1="0" y1="0" x2="0" y2="1">
          <stop offset="0" stop-color="#c9d3d8"/><stop offset="0.4" stop-color="#7f9463"/><stop offset="1" stop-color="#5d7048"/>
        </linearGradient>
        <linearGradient id="earth-site" x1="0" y1="0" x2="0" y2="1">
          <stop offset="0" stop-color="#a9c3d8"/><stop offset="0.45" stop-color="#b9a67a"/><stop offset="1" stop-color="#b77a5c"/>
        </linearGradient>
        <linearGradient id="blast-site" x1="0" y1="0" x2="1" y2="1">
          <stop offset="0" stop-color="#cfd8de"/><stop offset="0.5" stop-color="#8fb2c6"/><stop offset="1" stop-color="#9a9a9a"/>
        </linearGradient>
        <linearGradient id="red-fade" x1="0" y1="0" x2="1" y2="1">
          <stop offset="0" stop-color="#b23344"/><stop offset="1" stop-color="#8e2533"/>
        </linearGradient>
      </defs>
      <rect class="surface" width="450" height="1055" fill="#ffffff"/>
      <rect class="footer-panel" y="718" width="450" height="337" fill="#333333"/>

      <g role="img" aria-label="Excavator working beside a large launch assembly building">
        <polygon points="0,0 365,0 275,172 0,172" fill="url(#sky-site)"/>
      </g>
      <polygon class="accent-red" points="0,65 30,150 0,150" fill="#a32b38"/>
      <polygon class="accent-dark" points="450,0 450,185 350,185" fill="#333333"/>

      <polygon class="accent-red" points="0,220 90,220 0,440" fill="url(#red-fade)"/>
      <g role="img" aria-label="Aerial view of an industrial plant with a long conveyor over forest">
        <polygon points="195,172 450,172 450,330 380,330 400,377 115,377" fill="url(#green-site)"/>
      </g>
      <polygon class="accent-dark" points="372,330 450,330 450,520" fill="#333333"/>

      <g role="img" aria-label="Excavator and haul truck on a cleared red-earth site">
        <polygon points="0,377 255,377 340,582 0,582" fill="url(#earth-site)"/>
      </g>

      <g role="img" aria-label="Power station structure collapsing during demolition with smoke">
        <polygon points="140,582 450,582 450,750 380,750 390,787 225,787" fill="url(#blast-site)"/>
      </g>
      <polygon class="accent-red" points="0,672 178,672 200,718 0,718" fill="#d43d4b"/>
      <polygon class="accent-red" points="370,750 450,750 450,950" fill="#a32b38"/>
      <polygon class="accent-red" points="0,1020 130,1020 115,1055 0,1055" fill="#a32b38"/>
    </svg>

    <div class="brand"><span class="brand__mark"></span>R.K. HOLLOWAY Companies</div>
    <p class="tagline">
      <span class="tagline__lead">Building the Nation's</span>
      <span class="tagline__accent">horizon</span>
      <span class="tagline__since">since 1972.</span>
    </p>
  </section>

  <section class="banner banner--wave">
    <svg viewBox="0 0 390 1010" preserveAspectRatio="none">
      <defs>
        <linearGradient id="mono-site" x1="0" y1="0" x2="0" y2="1">
          <stop offset="0" stop-color="#d9d9d9"/><stop offset="0.5" stop-color="#8d8d8d"/><stop offset="1" stop-color="#6a6a6a"/>
        </linearGradient>
        <linearGradient id="wave-red" x1="0" y1="0" x2="1" y2="0">
          <stop offset="0" stop-color="#e0303e"/><stop offset="0.5" stop-color="#b7202f"/><stop offset="1" stop-color="#e44b5a"/>
        </linearGradient>
        <linearGradient id="wave-light" x1="0" y1="1" x2="1" y2="0">
          <stop offset="0" stop-color="#f09395"/><stop offset="1" stop-color="#e8485a"/>
        </linearGradient>
        <linearGradient id="paper" x1="0" y1="0" x2="1" y2="1">
          <stop offset="0" stop-color="#e6e6e6"/><stop offset="0.5" stop-color="#ffffff"/><stop offset="1" stop-color="#f3f3f3"/>
        </linearGradient>
      </defs>
      <rect class="surface" width="390" height="1010" fill="url(#paper)"/>
      <g role="img" aria-label="Black and white view of a multi-storey industrial building under demolition">
        <path d="M0,0 H390 V360 C320,360 270,400 230,440 C190,480 100,500 0,460 Z" fill="url(#mono-site)"/>
      </g>
      <path class="wave-red" d="M0,420 C40,520 140,560 220,520 C290,480 320,400 390,360 V470 C330,500 290,540 250,570 C200,600 130,560 80,560 C40,560 15,550 0,545 Z" fill="url(#wave-red)"/>
      <path class="wave-light" d="M390,380 V580 C340,582 300,585 250,590 C220,592 218,560 240,530 C290,470 340,420 390,380 Z" fill="url(#wave-light)"/>
      <path class="wave-dark" d="M0,930 C40,945 85,975 115,1010 H0 Z" fill="#1c1c1c"/>
      <path class="wave-dark" d="M195,1010 C250,975 330,960 390,950 V1010 Z" fill="#1c1c1c"/>
    </svg>

    <div class="brand"><span class="brand__mark"></span>R.K. HOLLOWAY Companies</div>
    <p class="tagline">
      <span class="tagline__lead">Building the Nation's</span>
      <span class="tagline__accent">horizon</span>
      <span class="tagline__since">since 1972.</span>
    </p>
  </section>

</main>
</body>
</html>
```